Business Card Design - Amberfield Court

We are looking at a new design for our business cards that has a modern and professional look. We run a residential aged care facility focussing on the care of residents. The cards will be used for potential clients, consultants and business opportunities in this sector. Blue and white is our main colours and would to see these colours incorporated in the design.
Industry/Entity Type
Business
Contact Information for Business Card
Amberfield Court, Darren Walsh, dwalsh@amberfieldcourt.com.au, Finance Manager, 0472 639 208, BCom, 37 Marrabel Crescent, Brindle Vale, Qld 4093.
Look and feel
Each slider illustrates characteristics of the customer's brand and the style your logo design should communicate.

```html
<!DOCTYPE html>
<html lang="en">
<head>
<meta charset="utf-8">
<title>Amberfield Court – Business Card</title>
<link href="https://fonts.googleapis.com/css2?family=Open+Sans:wght@400;600;700&family=Oswald:wght@500&display=swap" rel="stylesheet">
<style>
  :root {
    --brand-blue: #4a7a97;
    --brand-blue-deep: #3f6c88;
    --band-taupe: #b7aca5;
    --paper-white: #ffffff;
    --ink-slate: #3b4a55;
    --soft-white: #e7eef3;
    --muted-taupe: #a9b6bf;
    --backdrop: #e8e5e1;
  }
  * { box-sizing: border-box; margin: 0; padding: 0; }
  html, body {
    width: 1200px; height: 1023px; overflow: hidden;
    background: var(--backdrop);
    font-family: "Open Sans", Arial, sans-serif;
  }
  .card {
    position: absolute;
    width: 600px; height: 364px;
    border-radius: 4px;
    overflow: hidden;
    box-shadow: 0 6px 18px rgba(0,0,0,0.18);
  }

  /* Front */
  .card-front { left: 60px; top: 80px; background: var(--paper-white); }
  .front-white { position: absolute; left: 0; top: 0; width: 100%; height: 196px; }
  .brand-lockup {
    position: absolute; left: 110px; top: 104px;
    display: flex; align-items: center; gap: 16px;
  }
  .brand-dot {
    width: 64px; height: 64px; border-radius: 50%;
    background: var(--brand-blue);
    flex: none;
  }
  .brand-name {
    font-family: "Open Sans", Arial, sans-serif;
    font-weight: 400; font-size: 34px; letter-spacing: 4px;
    text-transform: uppercase; color: var(--ink-slate);
    white-space: nowrap;
  }
  .tagline-band {
    position: absolute; left: 0; top: 196px; width: 100%; height: 34px;
    background: var(--band-taupe);
  }
  .tagline {
    position: absolute; left: 0; width: 100%; top: 5px;
    text-align: center;
    font-size: 17px; color: var(--paper-white); letter-spacing: 0.5px;
    white-space: nowrap;
  }
  .front-blue {
    position: absolute; left: 0; top: 230px; width: 100%; height: 134px;
    background: var(--brand-blue);
  }
  .person { position: absolute; left: 34px; bottom: 26px; }
  .person-name {
    font-family: "Oswald", "Arial Narrow", sans-serif;
    font-weight: 500; font-size: 24px; letter-spacing: 1px;
    color: var(--paper-white); text-transform: uppercase; line-height: 1.1;
  }
  .person-role { font-size: 14px; color: var(--muted-taupe); margin-top: 2px; }
  .contact-list {
    position: absolute; right: 26px; top: 18px;
    list-style: none; text-align: right;
  }
  .contact-list li {
    display: flex; justify-content: flex-end; align-items: center; gap: 10px;
    font-size: 13px; color: var(--soft-white); line-height: 26px;
    white-space: nowrap;
  }
  .contact-list svg { width: 13px; height: 13px; fill: var(--soft-white); flex: none; }

  /* Back */
  .card-back { left: 560px; top: 580px; background: var(--brand-blue); }
  .back-lockup {
    position: absolute; left: 0; top: 118px; width: 100%;
    display: flex; justify-content: center; align-items: center; gap: 16px;
  }
  .back-lockup .brand-dot { background: var(--paper-white); }
  .back-lockup .brand-name { color: var(--paper-white); }
  .back-band {
    position: absolute; left: 120px; top: 198px;
    width: 360px; height: 32px; background: var(--band-taupe);
  }
  .back-band .tagline { top: 4px; }
</style>
</head>
<body>

<section class="card card-front">
  <div class="front-white">
    <div class="brand-lockup">
      <span class="brand-dot"></span>
      <span class="brand-name">Amberfield Court</span>
    </div>
  </div>
  <div class="tagline-band">
    <span class="tagline">Comfort, Respect, Belonging</span>
  </div>
  <div class="front-blue">
    <ul class="contact-list">
      <li>0472 639 208
        <svg viewBox="0 0 24 24" aria-hidden="true"><path d="M6.6 10.8a15 15 0 0 0 6.6 6.6l2.2-2.2c.3-.3.7-.4 1-.2 1.1.4 2.3.6 3.6.6.6 0 1 .4 1 1V20c0 .6-.4 1-1 1A17 17 0 0 1 3 4c0-.6.4-1 1-1h3.5c.6 0 1 .4 1 1 0 1.3.2 2.5.6 3.6.1.3 0 .7-.2 1z"/></svg>
      </li>
      <li>dwalsh@amberfieldcourt.com.au
        <svg viewBox="0 0 24 24" aria-hidden="true"><path d="M2 5h20v14H2zm2 2v.5l8 5 8-5V7z"/></svg>
      </li>
      <li>BCom, 37 Marrabel Crescent, Brindle Vale, Qld 4093
        <svg viewBox="0 0 24 24" aria-hidden="true"><path d="M12 2a7 7 0 0 0-7 7c0 5 7 13 7 13s7-8 7-13a7 7 0 0 0-7-7zm0 9.5a2.5 2.5 0 1 1 0-5 2.5 2.5 0 0 1 0 5z"/></svg>
      </li>
    </ul>
    <div class="person">
      <div class="person-name">Darren Walsh</div>
      <div class="person-role">Finance Manager</div>
    </div>
  </div>
</section>

<section class="card card-back">
  <div class="back-lockup">
    <span class="brand-dot"></span>
    <span class="brand-name">Amberfield Court</span>
  </div>
  <div class="back-band">
    <span class="tagline">Comfort, Respect, Belonging</span>
  </div>
</section>

</body>
</html>
```